Torvane Email Signature Banners – Fabrication Capability Series

www.Torvane.com.au is an Australian engineering and fabrication company specialising in fabrication and welding of :
steel piping spools,
skids and frames,
small volume process steel tanks
and general steel fabrication
We require four distinct banner designs for use in Microsoft Lintaro email signatures. Each banner will highlight a specific capability while maintaining a consistent brand identity.
Deliverables
Four banners total:
Piping Spools Fabrication – focus on precision welding and stainless steel pipework
Skid & Frames Fabrication – highlight skid systems and structural frames
Small Steel Tanks Fabrication – show fabricated tanks and workshop craftsmanship
General Fabrication Solutions – broad steel fabrication theme for company-wide use
Dimensions: 600–700 px wide × 100 px high
Format: PNG (preferred), small file size prefered
Resolution: 72 dpi
Background: non-transparent, industrial or workshop setting
Text examples:
1. Piping Spools Fabrication
Option A: “Expert Fabrication Solutions for Process Piping”
Option B: “Precision Welding for Complex Systems”
Option C: “Delivering Quality in Every Spool”
Option D: “Engineered for Flow, Built for Strength”
2. Skid & Frames Fabrication
Option A: “Custom Engineered Modular Systems”
Option B: “Built Strong. Designed Smart.”
Option C: “Reliable Frames for Industrial Performance”
Option D: “Modular Fabrication for Seamless Integration”
3. Small Steel Tanks Fabrication
Option A: “Precision Built for Your Needs”
Option B: “Compact Strength. Proven Durability.”
Option C: “Fabricated for Performance and Longevity”
Option D: “Small Tanks. Big Reliability.”
4. General Fabrication Solutions
Option A: “Quality Craftsmanship, Proven Results”
Option B: “Your Partner in Precision Fabrication”
Option C: “Engineering Excellence in Every Weld”
Option D: “Australian Fabrication. Global Standards.”
Style Direction
Clean, professional, and engineering‑focused
Use Torvane brand colours
Blend photo realism with vector clarity (no heavy gradients)
Include subtle industrial textures or workshop imagery
Typography: bold sans‑serif, legible at small scale
Usage Context
These banners will appear at the bottom of staff email signatures via Lintaro Email Signature Tool for Microsoft 365, so clarity and fast loading are essential. No Logo is required in the banners.
Reference
Existing Torvane signature is attached. Colour palette to match the signature style and logo.
Target Market(s)
Engineering and construction companies,
Industry/Entity Type
Engineering fabrication design
Look and feel

```html
<!DOCTYPE html>
<html lang="en">
<head>
<meta charset="utf-8">
<title>Fabrication Capability Banners</title>
<link rel="stylesheet" href="https://fonts.googleapis.com/css2?family=Montserrat:wght@800&family=Jost:wght@400;500&display=swap">
<style>
  :root {
    --page-bg: #ffffff;
    --brand-blue: #23a8e0;
    --divider-grey: #8a8d90;
    --text-white: #ffffff;
  }
  * { margin: 0; padding: 0; box-sizing: border-box; }
  html, body {
    width: 1200px;
    height: 1200px;
    overflow: hidden;
    background: var(--page-bg);
  }
  .banner-sheet {
    position: relative;
    width: 1200px;
    height: 1200px;
  }
  .banner {
    position: absolute;
    left: 146px;
    width: 916px;
    height: 152px;
    overflow: hidden;
  }
  .banner--spools { top: 230px; }
  .banner--skids { top: 428px; }
  .banner--tanks { top: 627px; }
  .banner--general { top: 825px; }

  .banner__art {
    position: absolute;
    inset: 0;
    width: 916px;
    height: 152px;
  }
  .banner__capability {
    position: absolute;
    left: 20px;
    top: 50%;
    transform: translateY(-50%);
    font-family: "Montserrat", Arial, sans-serif;
    font-weight: 800;
    font-size: 24px;
    line-height: 32px;
    letter-spacing: 1.8px;
    color: var(--text-white);
    text-transform: uppercase;
  }
  .banner__tagline {
    position: absolute;
    top: 50%;
    transform: translateY(-50%);
    font-family: "Jost", Arial, sans-serif;
    font-weight: 500;
    font-size: 30px;
    line-height: 36px;
    letter-spacing: 2px;
    color: var(--text-white);
    white-space: nowrap;
  }
  .banner--spools .banner__tagline { left: 316px; top: 48%; }
  .banner--skids .banner__tagline { left: 400px; }
  .banner--tanks .banner__tagline { left: 355px; top: 48%; }
  .banner--general .banner__tagline { left: 403px; }
</style>
</head>
<body>
<main class="banner-sheet">

  <section class="banner banner--spools">
    <svg class="banner__art" viewBox="0 0 916 152">
      <defs>
        <linearGradient id="photo-spools" x1="0" y1="0" x2="1" y2="1">
          <stop offset="0" stop-color="#45474a"/>
          <stop offset="0.5" stop-color="#2f3134"/>
          <stop offset="1" stop-color="#232426"/>
        </linearGradient>
      </defs>
      <rect width="916" height="152" fill="url(#photo-spools)" role="img" aria-label="Darkened workshop photo of stainless steel piping spools with flanges"/>
      <polygon points="0,0 145,0 301,152 0,152" fill="var(--brand-blue)"/>
      <line x1="145" y1="0" x2="301" y2="152" stroke="var(--divider-grey)" stroke-width="3"/>
      <polygon points="818,0 828,0 916,90 916,100" fill="var(--brand-blue)"/>
      <polygon points="848,0 858,0 916,60 916,70" fill="var(--brand-blue)"/>
    </svg>
    <h2 class="banner__capability">Piping<br>Spools<br>Fabrication</h2>
    <p class="banner__tagline">Delivering Quality in Every Spool</p>
  </section>

  <section class="banner banner--skids">
    <svg class="banner__art" viewBox="0 0 916 152">
      <defs>
        <linearGradient id="photo-skids" x1="0" y1="0" x2="1" y2="1">
          <stop offset="0" stop-color="#2c2b2a"/>
          <stop offset="0.5" stop-color="#232221"/>
          <stop offset="1" stop-color="#1a1a1a"/>
        </linearGradient>
      </defs>
      <rect width="916" height="152" fill="url(#photo-skids)" role="img" aria-label="Darkened workshop photo of a fabricated steel skid frame on trestles"/>
      <polygon points="0,0 145,0 301,152 0,152" fill="var(--brand-blue)"/>
      <line x1="145" y1="0" x2="301" y2="152" stroke="var(--divider-grey)" stroke-width="3"/>
      <polygon points="818,0 828,0 916,90 916,100" fill="var(--brand-blue)"/>
      <polygon points="848,0 858,0 916,60 916,70" fill="var(--brand-blue)"/>
    </svg>
    <h2 class="banner__capability">Skid &amp;<br>Frames<br>Fabrication</h2>
    <p class="banner__tagline">Reliable Frames for<br>Industrial Performance</p>
  </section>

  <section class="banner banner--tanks">
    <svg class="banner__art" viewBox="0 0 916 152">
      <defs>
        <linearGradient id="photo-tanks" x1="0" y1="0" x2="1" y2="1">
          <stop offset="0" stop-color="#4a4b4d"/>
          <stop offset="0.5" stop-color="#2e2f31"/>
          <stop offset="1" stop-color="#1f2022"/>
        </linearGradient>
      </defs>
      <rect width="916" height="152" fill="url(#photo-tanks)" role="img" aria-label="Darkened workshop photo of small fabricated stainless steel tanks"/>
      <polygon points="0,0 145,0 301,152 0,152" fill="var(--brand-blue)"/>
      <line x1="145" y1="0" x2="301" y2="152" stroke="var(--divider-grey)" stroke-width="3"/>
      <polygon points="818,0 828,0 916,90 916,100" fill="var(--brand-blue)"/>
      <polygon points="848,0 858,0 916,60 916,70" fill="var(--brand-blue)"/>
    </svg>
    <h2 class="banner__capability">Small<br>Steel Tanks<br>Fabrication</h2>
    <p class="banner__tagline">Small Tanks. Big Reliability.</p>
  </section>

  <section class="banner banner--general">
    <svg class="banner__art" viewBox="0 0 916 152">
      <defs>
        <linearGradient id="photo-general" x1="0" y1="0" x2="1" y2="1">
          <stop offset="0" stop-color="#2a2a2b"/>
          <stop offset="0.5" stop-color="#222223"/>
          <stop offset="1" stop-color="#19191a"/>
        </linearGradient>
      </defs>
      <rect width="916" height="152" fill="url(#photo-general)" role="img" aria-label="Darkened photo of a steel fabrication workshop floor with beams and machinery"/>
      <polygon points="0,0 145,0 301,152 0,152" fill="var(--brand-blue)"/>
      <line x1="145" y1="0" x2="301" y2="152" stroke="var(--divider-grey)" stroke-width="3"/>
      <polygon points="818,0 828,0 916,90 916,100" fill="var(--brand-blue)"/>
      <polygon points="848,0 858,0 916,60 916,70" fill="var(--brand-blue)"/>
    </svg>
    <h2 class="banner__capability">General<br>Fabrication<br>Solutions</h2>
    <p class="banner__tagline">Australian Fabrication.<br>Global Standards.</p>
  </section>

</main>
</body>
</html>
```